Personal Trainer website design

We are working with a personal trainer to design a website. They offer their primary services: Diet Coaching, In-Person Coaching (workouts), and Remote Coaching.
Some sites we like: https://www.mirabelthorne.com, https://kavialune.com/en-us, https://corvexfit.co.uk
Thank you for taking the time to consider designing a website for us. We are web developers based in Stockton, CA USA. Most of our projects go through the same process. Understanding this process may help you win a project with us. We custom-code all of our websites in-house. We don’t have any requirements as to what tools you use for your design, but ask that you follow these guidelines.
IMAGES:
We ask that if you use any images, or icons in the design, have a link to the asset, so we can purchase the image/icon. Most of the designs we submit do not have the customer’s images on them unless they have some great images. Be creative; show us the feeling that you are trying to portray with your image choices. Use any royalty-free site you choose. We subscribe to Quillon and mostly use their images, but are ok to purchase images outside of Quillon.
FONTS:
We ask that you identify the fonts you’re using in the design. This can be done in a message if you want. We typically use Brivane Fonts and Quillon Fonts.
CONTENT:
We're always open to different content and ideas. Often, we submit designs with stock images so that the client can see our vision. We typically go back and take pictures after the website launch to use their images with our vision. Lorem Ipsum is fine for paragraphs, but we ask that you make the Headers with correct English. We want to be able to show the vision and identify the sections of the website.
INSPIRATION:
We try and add a couple of links in the brief of some websites that we like to help you get started in your design.
REVISIONS:
We do not often ask for revisions of the designs unless we see something in the design that may not appeal to the client. If there are slight changes that we want to make, we simply do that in the development process.
FEEDBACK:
We rarely give feedback on designs during the design process. We are working on many website projects and do not have the time to give feedback. We usually respond if your request is well thought out and asks specific questions, but a note asking “feedback, please” usually goes unanswered.
1 page

```html
<!DOCTYPE html>
<html lang="en">
<head>
<meta charset="utf-8">
<title>Orbitfit — Personal Training</title>
<link href="https://fonts.googleapis.com/css2?family=Teko:wght@500;600;700&family=Roboto:wght@400;500;700&display=swap" rel="stylesheet">
<style>
:root{
  --olive:#8a9418;
  --olive-dark:#6f7812;
  --maroon:#5c0b05;
  --ink:#2a2a2a;
  --text:#333;
  --white:#fff;
  --footer:#2b2b2b;
}
*{box-sizing:border-box;margin:0;padding:0}
html,body{width:1200px;height:2961px;overflow:hidden}
body{position:relative;font-family:"Roboto",sans-serif;color:var(--text);background:var(--white)}
.abs{position:absolute}
.display{font-family:"Teko",sans-serif;font-weight:700;letter-spacing:2px;text-transform:uppercase;line-height:1}

/* header */
.site-header{left:0;top:0;width:1200px;height:115px;background:var(--white)}
.brand{left:110px;top:38px;display:flex;align-items:center;gap:10px;font-family:"Roboto",sans-serif;font-weight:700;font-size:34px;color:var(--ink);letter-spacing:1px}
.brand-dot{width:16px;height:16px;border-radius:50%;background:var(--olive)}
.nav{left:411px;top:49px;display:flex;gap:0;font-size:16px}
.nav a{color:var(--ink);text-decoration:none;margin-right:29px}
.nav a.active{color:var(--olive);font-weight:500}
.btn-start{left:955px;top:34px;width:133px;height:48px;border-radius:24px;background:linear-gradient(90deg,var(--olive),var(--maroon));color:#fff;font-weight:700;font-size:15px;display:flex;align-items:center;justify-content:center}

/* hero */
.hero{left:0;top:115px;width:1200px;height:540px;background:linear-gradient(100deg,#4a3b30 0%,#2d2520 40%,#1f1c1a 100%)}
.hero-dots{left:44px;top:272px}
.hero-dots span{display:block;width:11px;height:11px;border-radius:50%;background:#fff;margin-bottom:32px}
.hero-dots span.on{background:var(--olive)}
.hero-ghost-top{left:552px;top:215px;font-size:86px;color:transparent;-webkit-text-stroke:1.5px rgba(255,255,255,.45)}
.hero-ghost-big{left:556px;top:330px;font-size:210px;color:transparent;-webkit-text-stroke:1.5px rgba(255,255,255,.35);letter-spacing:6px}
.hero-welcome{left:618px;top:248px;font-size:58px;color:#fff}
.hero-title{left:618px;top:325px;font-size:132px;color:#fff;letter-spacing:6px}
.hero-curve{left:0;top:555px}

/* section titles */
.section-title{left:0;width:1200px;text-align:center;font-size:64px}
.section-title .a{color:var(--olive)}
.section-title .b{color:var(--maroon)}

/* services */
.service-card{top:720px;width:267px;height:357px;border-radius:14px;overflow:hidden;background:#fff;box-shadow:0 4px 14px rgba(0,0,0,.15)}
.service-img{position:absolute;left:0;top:0;width:100%;height:300px}
.service-label{position:absolute;left:24px;top:322px;font-size:15px;font-weight:500;letter-spacing:.5px;color:var(--ink)}
.service-arrow{position:absolute;top:318px}
.service-corner{position:absolute;right:0;top:300px}
.mascot{border-radius:50%;background:radial-gradient(circle at 50% 45%,#e8e8e8 0 30%,var(--olive) 31%)}

/* about */
.about-frame{left:112px;top:1265px;width:1008px;height:425px;border:2px solid var(--ink);border-radius:60px}
.about-photo{left:207px;top:1165px;width:993px;height:507px;border-radius:60px 0 0 60px;background:linear-gradient(120deg,#6b5546,#3d4a55 55%,#9aa3ab)}
.about-panel{left:0;top:1307px}
.about-title{left:110px;top:1345px;font-size:60px;color:#fff}
.about-title .b{color:var(--maroon)}
.about-text{left:111px;top:1425px;width:437px;color:#fff;font-size:17px;line-height:30px;text-align:justify}
.about-link{left:115px;top:1600px;color:#fff;font-weight:700;font-size:17px;text-decoration:underline}

/* testimonials */
.avatar{left:112px;top:1890px;width:86px;height:86px;border-radius:12px 0 0 0;background:linear-gradient(#b59b84,#4b3f38)}
.avatar-frame{left:124px;top:1902px;width:78px;height:78px;border:1px solid var(--ink)}
.client-name{left:230px;top:1905px;font-size:19px;color:var(--ink)}
.client-role{left:230px;top:1933px;font-size:15px;color:var(--ink)}
.client-stars{left:230px;top:1956px;font-size:12px;color:#f2b705;letter-spacing:1px}
.quote-mark{left:530px;top:1880px;font-family:"Teko",sans-serif;font-size:150px;line-height:1;color:#c9a4a0}
.slider-btn{left:47px;width:26px;height:26px;border-radius:50%}
.client-text{left:114px;top:1999px;width:504px;font-size:17px;line-height:27.5px;color:var(--ink);text-align:justify}
.client-photo{left:778px;top:1864px;width:311px;height:304px;border-radius:12px;background:linear-gradient(135deg,#8a8a45,#3c4a2a 60%,#2d4058)}

/* contact */
.contact{left:0;top:2246px;width:1200px;height:570px;background:linear-gradient(120deg,#a2a83a,#8f9722 50%,#a6ad45)}
.contact-title{left:0;top:2305px;width:1200px;text-align:center;font-size:60px;color:#fff}
.contact-title .b{color:var(--maroon)}
.field{background:#fff;border-radius:14px;font-size:17px;color:#555;padding:0 19px;display:flex;align-items:center}
.field.area{align-items:flex-start;padding-top:22px}
.btn-send{left:534px;top:2718px;width:132px;height:48px;border-radius:24px;background:var(--maroon);color:#fff;font-weight:700;font-size:16px;display:flex;align-items:center;justify-content:center}

/* footer */
.site-footer{left:0;top:2816px;width:1200px;height:145px;background:var(--footer);color:#fff}
.footer-nav{position:absolute;left:287px;top:50px;display:flex;font-size:19px;font-weight:500}
.footer-nav span{margin-right:36px}
.copyright{position:absolute;left:0;top:106px;width:1200px;text-align:center;font-size:17px}
</style>
</head>
<body>

<header class="site-header abs">
  <div class="brand abs"><span>ORBITFIT</span><span class="brand-dot"></span></div>
  <nav class="nav abs">
    <a class="active">Home</a><a>About</a><a>Services</a><a style="margin-right:30px">Coaches</a><a>Testimonials</a><a>Contact</a>
  </nav>
  <div class="btn-start abs">Get Started</div>
</header>

<section class="hero abs" role="img" aria-label="Woman training with battle ropes in a dark gym"></section>
<div class="hero-dots abs"><span></span><span></span><span></span><span class="on"></span></div>
<div class="hero-ghost-top display abs">Welcome to</div>
<div class="hero-ghost-big display abs">Orbitfit</div>
<div class="hero-welcome display abs">Welcome to</div>
<div class="hero-title display abs">Orbitfit</div>
<svg class="hero-curve abs" width="1200" height="100" viewBox="0 0 1200 100">
  <path d="M0 90 Q600 -70 1200 90 L1200 100 L0 100 Z" fill="#8a9418"/>
  <path d="M0 100 Q600 -50 1200 100 Z" fill="#fff"/>
</svg>

<h2 class="section-title display abs" style="top:625px"><span class="a">Our</span> <span class="b">Services</span></h2>

<article class="service-card abs" style="left:147px">
  <div class="service-img" role="img" aria-label="Woman eating a fresh salad after a workout" style="background:linear-gradient(135deg,#9bb0b4,#7c8a3a 60%,#b8a48c)"></div>
  <span class="service-label">DIET COACHING</span>
  <svg class="service-arrow" style="left:172px" width="46" height="20" viewBox="0 0 46 20"><path d="M2 10H42M34 3l8 7-8 7" fill="none" stroke="#222" stroke-width="1.6"/></svg>
  <svg class="service-corner" width="40" height="57" viewBox="0 0 40 57"><path d="M0 0H40V57Z" fill="#222"/></svg>
</article>
<article class="service-card abs" style="left:467px">
  <div class="service-img" role="img" aria-label="Trainer guiding a client through lunges in a brick gym" style="background:linear-gradient(135deg,#b6a79a,#5d4b42 55%,#c9c3bb)"></div>
  <span class="service-label">IN-PERSON COACHING</span>
  <svg class="service-arrow" style="left:208px" width="14" height="20" viewBox="0 0 14 20"><path d="M3 3l7 7-7 7" fill="none" stroke="#222" stroke-width="1.8"/></svg>
  <svg class="service-corner" width="40" height="57" viewBox="0 0 40 57"><path d="M0 0H40V57Z" fill="#222"/></svg>
</article>
<article class="service-card abs" style="left:788px">
  <div class="service-img" role="img" aria-label="Man filming a home workout with a phone on a tripod" style="background:linear-gradient(135deg,#8e9094,#4a4c50 55%,#b9b9bb)"></div>
  <span class="service-label">REMOTE COACHING</span>
  <svg class="service-arrow" style="left:206px" width="14" height="20" viewBox="0 0 14 20"><path d="M3 3l7 7-7 7" fill="none" stroke="#222" stroke-width="1.8"/></svg>
  <svg class="service-corner" width="40" height="57" viewBox="0 0 40 57"><path d="M0 0H40V57Z" fill="#222"/></svg>
</article>
<div class="mascot abs" role="img" aria-label="Astronaut mascot holding a flag" style="left:1060px;top:1032px;width:140px;height:140px"></div>

<div class="about-frame abs"></div>
<div class="about-photo abs" role="img" aria-label="Woman doing push-ups on kettlebells in a gym"></div>
<svg class="about-panel abs" width="665" height="365" viewBox="0 0 665 365"><path d="M0 0H525L665 365H0Z" fill="#8a9418"/></svg>
<h2 class="about-title display abs">About <span class="b">Us</span></h2>
<p class="about-text abs">Lorem ipsum dolor sit amet, consectetur adipiscing elit, sed do eiusmod tempor incididunt ut labore et dolore magna aliqua. Quis ipsum suspendisse ultrices gravida. Risus commodo viverra maecenas accumsan lacus vel facilisis. Lbore et dolore magna aliqua.</p>
<a class="about-link abs">Learn More</a>

<h2 class="section-title display abs" style="top:1778px"><span class="a">Happy</span> <span class="b">Clients</span></h2>
<div class="avatar abs" role="img" aria-label="Client portrait"></div>
<div class="avatar-frame abs"></div>
<div class="client-name abs">Dale Marrow</div>
<div class="client-role abs">Lorem Ipsum</div>
<div class="client-stars abs">★★★★★</div>
<div class="quote-mark abs">”</div>
<svg class="slider-btn abs" style="top:2001px" viewBox="0 0 26 26"><circle cx="13" cy="13" r="13" fill="#5c0b05"/><path d="M10 8l5 5-5 5" fill="none" stroke="#fff" stroke-width="2.2"/></svg>
<svg class="slider-btn abs" style="top:2045px" viewBox="0 0 26 26"><circle cx="13" cy="13" r="13" fill="#cfcfcf"/><path d="M16 8l-5 5 5 5" fill="none" stroke="#fff" stroke-width="2.2"/></svg>
<p class="client-text abs">Lorem ipsum dolor sit amet, consectetur adipiscing elit, sed do eiusmod tempor incididunt ut labore et dolore magna aliqua. Ut enim ad minim veniam, quis nostrud exercitation ullamco laboris nisi ut aliquip ex ea commodo consequat. Duis aute irure dolor in reprehenderit in voluptate velit esse cillum dolore.</p>
<div class="client-photo abs" role="img" aria-label="Smiling older man jogging outdoors"></div>
<div class="mascot abs" role="img" aria-label="Astronaut mascot holding a flag" style="left:698px;top:2044px;width:138px;height:138px"></div>

<section class="contact abs" role="img" aria-label="Olive-tinted photo of a man training in a gym"></section>
<h2 class="contact-title display abs">Contact <span class="b">Us</span></h2>
<div class="field abs" style="left:309px;top:2408px;width:281px;height:67px">First Name *</div>
<div class="field abs" style="left:609px;top:2408px;width:281px;height:67px">Last Name *</div>
<div class="field abs" style="left:310px;top:2494px;width:580px;height:67px">Email ID *</div>
<div class="field area abs" style="left:310px;top:2578px;width:580px;height:109px">Message *</div>
<div class="btn-send abs">Send</div>

<footer class="site-footer abs">
  <div class="footer-nav"><span>Home</span><span>About</span><span style="margin-right:41px">Services</span><span>Coaches</span><span style="margin-right:41px">Testimonials</span><span>Contact</span></div>
  <div class="copyright">2023 Orbitfit. All Rights Reserved.</div>
</footer>

</body>
</html>
```